Modern Business Card for Larkwell 2018

Our company assumes the best about people. We are creating an online community of entrepreneurs and business leaders who struggle with marketing their business online.

This business card should POP! We recently got a new logo and are launching a new website next month, so our business cards should make a statement that feels:
-Fresh
-Smart
-Trustworthy
-Fun

Target Market(s)

small business owners, entrepreneurs

Industry/Entity Type

Digital Marketing

Contact Information for Business Card

Dimensions: 3.5" x 2"

Font styles to use
Sans Serif

Colors
f37122
ffffff

Requirements
Must have
• We need a business card with a modern, bold design. We will use one side of the card as a lead-generation offer, so text on one side will need to fit up to 140 characters. The business card should stick to our core colors (orange, black, and white).
Nice to have
• We think a vertical "portrait" design could be interesting.
Should not have
• Should not look like a traditional business card. The round icon should stand out from a distance.

```html
<!DOCTYPE html>
<html lang="en">
<head>
<meta charset="utf-8">
<title>Larkwell Business Card</title>
<link rel="stylesheet" href="https://fonts.googleapis.com/css2?family=Open+Sans:wght@400;600;700;800&display=swap">
<style>
  :root {
    --orange: #f37122;
    --white: #ffffff;
    --black: #1a1a1a;
    --grey: #555555;
    --stage: #e6e6e6;
    --field-line: #8a8a8a;
  }
  * { box-sizing: border-box; margin: 0; padding: 0; }
  html, body {
    width: 1200px; height: 960px; overflow: hidden;
    background: var(--stage);
    font-family: "Open Sans", sans-serif;
  }
  .stage { position: relative; width: 1200px; height: 960px; }
  .card {
    position: absolute; left: 250px; width: 700px; height: 400px;
    overflow: hidden; box-shadow: 0 6px 18px rgba(0,0,0,0.18);
  }

  /* Offer side */
  .card--offer { top: 60px; background: var(--orange); color: var(--white); }
  .offer-mark {
    position: absolute; left: 70px; top: 40px; width: 180px; height: 180px;
    border-radius: 50%; background: var(--white);
  }
  .offer-divider {
    position: absolute; left: 300px; top: 40px; width: 2px; height: 210px;
    background: rgba(255,255,255,0.45);
  }
  .offer-copy { position: absolute; left: 335px; top: 38px; width: 330px; }
  .offer-headline {
    font-weight: 800; font-size: 27px; line-height: 1.05; text-transform: uppercase;
    letter-spacing: 0.2px;
  }
  .offer-body { margin-top: 10px; font-size: 18px; line-height: 1.25; font-weight: 400; }
  .offer-url { margin-top: 12px; font-size: 21px; font-weight: 700; }
  .offer-field {
    position: absolute; left: 60px; top: 272px; width: 600px; height: 96px;
    background: var(--white); border-radius: 18px;
  }
  .offer-field .rule {
    position: absolute; left: 30px; right: 30px; height: 1px; background: var(--field-line);
  }
  .offer-field .rule--one { top: 36px; }
  .offer-field .rule--two { top: 68px; }

  /* Contact side */
  .card--contact { top: 500px; background: var(--white); }
  .contact-band {
    position: absolute; left: 0; top: 36px; width: 100%; height: 110px;
    background: var(--orange);
  }
  .brand {
    position: absolute; left: 0; top: 50px; width: 100%; text-align: center;
  }
  .brand-dot {
    display: block; margin: 0 auto 28px; width: 72px; height: 72px;
    border-radius: 50%; background: var(--white);
  }
  .brand-name {
    display: block; font-weight: 800; font-size: 58px; line-height: 1;
    color: var(--black); letter-spacing: 2px; text-transform: uppercase;
  }
  .brand-tagline {
    display: block; margin-top: 8px; font-size: 15px; font-weight: 600; line-height: 1.2;
    letter-spacing: 2px; text-transform: uppercase; color: var(--black);
  }
  .contact {
    position: absolute; left: 0; top: 272px; width: 100%; text-align: center;
  }
  .contact-name {
    font-weight: 700; font-size: 26px; color: var(--orange); text-transform: uppercase;
    line-height: 1.15;
  }
  .contact-role {
    font-weight: 700; font-size: 20px; color: var(--black); text-transform: uppercase;
    line-height: 1.2;
  }
  .contact-email { font-size: 20px; color: var(--grey); line-height: 1.3; }
</style>
</head>
<body>
<main class="stage">

  <section class="card card--offer" aria-label="Offer side of card">
    <span class="offer-mark" aria-hidden="true"></span>
    <span class="offer-divider" aria-hidden="true"></span>
    <div class="offer-copy">
      <p class="offer-headline">Reach more people.<br>Make more money.<br>Create more impact.</p>
      <p class="offer-body">Get your free Larkwell Starter Package and our marketing guide today at</p>
      <p class="offer-url">Larkwellnow.com/start</p>
    </div>
    <div class="offer-field" aria-label="Write-in field">
      <span class="rule rule--one"></span>
      <span class="rule rule--two"></span>
    </div>
  </section>

  <section class="card card--contact" aria-label="Contact side of card">
    <span class="contact-band" aria-hidden="true"></span>
    <div class="brand">
      <span class="brand-dot" aria-hidden="true"></span>
      <span class="brand-name">Larkwell</span>
      <span class="brand-tagline">Share stories that move people</span>
    </div>
    <div class="contact">
      <p class="contact-name">Dana Whitlow</p>
      <p class="contact-role">Story Marketing Coach</p>
      <p class="contact-email">dana@larkwellnow.com</p>
    </div>
  </section>

</main>
</body>
</html>
```